Velk Partners Building Business Cards

We need a business card that reflects our business as "Solar Experts" in San Diego. Browse our website www.velkpartners.example our License needs to be displayed as "CSLB# 3867140" our phone number is (619) 555-0187

Save thousands on your electric bills and increase the value of your home while helping to protect the environment. Our solar installation experts will help you design the system that's right for you, using only the highest quality equipment that will look great and give you ideal performance. Our goal is to make you energy independent, and get your electric bill to 0.

Paul Osterby
(619) 555-0187
paul@velkpartners.example

Target Market(s)

Home owners in san diego looking for solar

Industry/Entity Type

Solar Energy

Contact Information for Business Card

Paul Osterby
(619) 555-0187
paul@velkpartners.example

Font styles to use
Other font styles liked:
• Use our logo font

Requirements
Must have
• License needs to be displayed as "CSLB# 3867140" our phone number is (619) 555-0187
Nice to have
• Real images of rooftop home solar in san diego
Should not have
• our business address

```html
<!DOCTYPE html>
<html lang="en">
<head>
<meta charset="utf-8">
<title>Velk Partners Building – Business Card</title>
<link rel="stylesheet" href="https://fonts.googleapis.com/css2?family=Open+Sans:wght@400;600;700&display=swap">
<style>
  :root {
    --navy: #1d3f7e;
    --navy-deep: #16336a;
    --sun: #f6b51e;
    --paper: #ffffff;
    --stage: #e9e9ec;
    --ink-soft: #3a3a3a;
  }
  html, body {
    margin: 0;
    padding: 0;
    width: 1200px;
    height: 950px;
    overflow: hidden;
    background: var(--stage);
    font-family: "Open Sans", Arial, sans-serif;
  }
  .sheet {
    position: relative;
    width: 1200px;
    height: 950px;
  }
  .card {
    position: absolute;
    left: 250px;
    width: 700px;
    height: 400px;
    background: var(--paper);
    box-shadow: 0 6px 18px rgba(0,0,0,0.18);
    overflow: hidden;
  }
  .card--front { top: 55px; }
  .card--back  { top: 495px; }

  .card__wave {
    position: absolute;
    inset: 0;
    width: 700px;
    height: 400px;
  }

  .brand {
    position: absolute;
    display: flex;
    align-items: center;
    gap: 12px;
  }
  .brand__dot {
    width: 22px;
    height: 22px;
    border-radius: 50%;
    background: var(--sun);
    flex: none;
  }
  .brand__name {
    font-weight: 700;
    color: var(--navy);
    line-height: 1.05;
    letter-spacing: -0.5px;
  }
  .card--front .brand { left: 42px; top: 168px; }
  .card--front .brand__name { font-size: 30px; width: 210px; }

  .contact {
    position: absolute;
    right: 34px;
    top: 36px;
    margin: 0;
    padding: 0;
    list-style: none;
    color: var(--paper);
    font-size: 15px;
    text-align: right;
  }
  .contact__item {
    display: flex;
    justify-content: flex-end;
    align-items: center;
    gap: 10px;
    height: 26px;
  }
  .contact__icon {
    width: 16px;
    height: 16px;
    flex: none;
  }

  .person {
    position: absolute;
    left: 300px;
    bottom: 34px;
    color: var(--paper);
  }
  .person__name {
    margin: 0;
    font-size: 22px;
    font-weight: 600;
  }
  .person__role {
    margin: 2px 0 0;
    font-size: 15px;
    color: var(--sun);
  }

  .card--back .brand { right: 70px; bottom: 70px; }
  .card--back .brand__name { font-size: 26px; }
  .card--back .brand__dot { width: 40px; height: 40px; }
  .back__web {
    position: absolute;
    left: 70px;
    bottom: 78px;
    margin: 0;
    font-size: 14px;
    font-style: normal;
    color: var(--ink-soft);
  }
</style>
</head>
<body>
<main class="sheet">

  <section class="card card--front" aria-label="Business card front">
    <svg class="card__wave" viewBox="0 0 700 400" aria-hidden="true">
      <path d="M448,0 C358,80 398,250 238,330 C198,355 168,380 158,400 L700,400 L700,0 Z" fill="var(--sun)"/>
      <path d="M458,0 C368,80 408,250 248,330 C208,355 178,380 168,400 L700,400 L700,0 Z" fill="var(--paper)"/>
      <path d="M472,0 C382,80 422,250 262,330 C222,355 192,380 182,400 L700,400 L700,0 Z" fill="var(--navy)"/>
      <path d="M510,0 C430,80 460,250 300,335 C260,358 240,385 232,400 L700,400 L700,0 Z" fill="var(--navy-deep)" opacity="0.35"/>
    </svg>

    <div class="brand">
      <span class="brand__dot"></span>
      <span class="brand__name">Velk Partners Building</span>
    </div>

    <ul class="contact">
      <li class="contact__item">CSLB# 3867140</li>
      <li class="contact__item">(619) 555-0187
        <svg class="contact__icon" viewBox="0 0 16 16" aria-hidden="true"><circle cx="8" cy="8" r="8" fill="var(--sun)"/><path d="M5,4 L7,4 L7.5,6.5 L6.5,7.2 C7,8.4 7.7,9.1 8.8,9.6 L9.5,8.5 L12,9 L12,11 C8,11.5 4.5,8 5,4 Z" fill="var(--navy)"/></svg>
      </li>
      <li class="contact__item">paul@velkpartners.example
        <svg class="contact__icon" viewBox="0 0 16 16" aria-hidden="true"><circle cx="8" cy="8" r="8" fill="var(--sun)"/><rect x="4" y="5" width="8" height="6" fill="none" stroke="var(--navy)" stroke-width="1.2"/><path d="M4,5 L8,8.5 L12,5" fill="none" stroke="var(--navy)" stroke-width="1.2"/></svg>
      </li>
      <li class="contact__item">www.velkpartners.example
        <svg class="contact__icon" viewBox="0 0 16 16" aria-hidden="true"><circle cx="8" cy="8" r="8" fill="var(--sun)"/><circle cx="8" cy="8" r="4" fill="none" stroke="var(--navy)" stroke-width="1.2"/><path d="M4,8 L12,8 M8,4 C6,6.5 6,9.5 8,12 M8,4 C10,6.5 10,9.5 8,12" fill="none" stroke="var(--navy)" stroke-width="1"/></svg>
      </li>
    </ul>

    <div class="person">
      <p class="person__name">Paul Osterby</p>
      <p class="person__role">CEO/Founder</p>
    </div>
  </section>

  <section class="card card--back" aria-label="Business card back">
    <address class="back__web">www.velkpartners.example</address>
    <div class="brand">
      <span class="brand__dot"></span>
      <span class="brand__name">Velk Partners Building</span>
    </div>
  </section>

</main>
</body>
</html>
```